BUSINESS CARD - HALLORAN FIELD SERVICES

I would like to create a business card for my fertilizer spreading business. I would like to incorporate my existing logo and also a description of the services offered. The business card will be given to farmers so must be kept simple but effective. It will also be left in stores so much also be eye catching in order to stand out from other cards.

Target Market(s)

FARMERS

Requirements
Must have
• FRONT OF CARD = EXISTING LOGO + "CUSTOMISED SPREADING" below the logo

REAR Of CARD = SERVICES OFFERED AND CONTACT DETAILS

- Bulk fertilizer including Lime, Gypsum, Manure & Compost
- Granular fertilizer including Single Super, Urea, Gran-am, & Custom Blends
- Modern equipment - Autosteer & Variable Rate Capable
- Friendly & Reliable Service
- Contact Gus: 0417 552 308
Nice to have
• utilize same color scheme as existing logo

```html
<!DOCTYPE html>
<html lang="en">
<head>
<meta charset="utf-8">
<title>Halloran Field Services – Business Card</title>
<link rel="stylesheet" href="https://fonts.googleapis.com/css2?family=Oswald:wght@500&family=Montserrat:wght@700;800&family=Open+Sans:ital,wght@0,400;0,700;1,400&display=swap">
<style>
  :root {
    --bg: #6e6e70;
    --card: #ffffff;
    --ink: #4d4d4f;
    --orange: #f7941d;
    --wheat-light: #fbe7a6;
    --wheat-deep: #f2bd3a;
  }
  * { box-sizing: border-box; margin: 0; padding: 0; }
  html, body { width: 1200px; height: 1200px; overflow: hidden; }
  body { background: var(--bg); position: relative; font-family: "Open Sans", Arial, sans-serif; }

  .card { position: absolute; width: 480px; height: 840px; background: var(--card); overflow: hidden; }
  .card--front { left: 101px; top: 84px; }
  .card--back  { left: 629px; top: 288px; height: 838px; }

  .brand { position: absolute; left: 0; right: 0; text-align: center; }
  .brand__dot { display: block; margin: 0 auto; border-radius: 50%; background: var(--ink); }
  .brand__name {
    display: block; color: var(--ink);
    font-family: "Montserrat", Arial, sans-serif; font-weight: 700;
    letter-spacing: -0.5px; line-height: 1.1;
  }
  .card--front .brand { top: 34px; }
  .card--front .brand__dot { width: 150px; height: 150px; }
  .card--front .brand__name { font-size: 34px; margin-top: 30px; }
  .card--back .brand { top: 30px; }
  .card--back .brand__dot { width: 104px; height: 104px; }
  .card--back .brand__name { font-size: 24px; margin-top: 22px; }

  .headline {
    position: absolute; left: 0; right: 0; top: 340px; text-align: center;
    font-family: "Oswald", "Arial Narrow", sans-serif; font-weight: 500;
    font-size: 84px; line-height: 1.16; letter-spacing: 0;
    white-space: nowrap;
  }
  .headline__top { display: block; color: var(--orange); }
  .headline__bottom { display: block; color: var(--ink); }

  .services { position: absolute; left: 72px; right: 30px; top: 226px; list-style: none; }
  .service { position: relative; padding-left: 36px; margin-bottom: 16px; }
  .service__tick { position: absolute; left: 0; top: 3px; width: 24px; height: 24px; }
  .service__title {
    display: block; color: var(--orange); font-weight: 700; font-size: 22px; line-height: 1.2;
  }
  .service__detail { display: block; color: var(--ink); font-size: 21px; line-height: 1.25; }

  .field {
    position: absolute; left: 0; right: 0;
    background: linear-gradient(180deg, var(--wheat-light) 0%, var(--wheat-deep) 55%, var(--wheat-light) 100%);
  }
  .card--front .field { top: 594px; height: 168px; }
  .card--back .field { top: 594px; height: 162px; }

  .contact {
    position: absolute; left: 0; right: 0; bottom: 0; height: 78px;
    background: var(--orange); text-align: center;
    font-family: "Montserrat", Arial, sans-serif; font-weight: 800;
    font-size: 36px; line-height: 80px; letter-spacing: 0.5px;
  }
  .card--back .contact { height: 82px; line-height: 84px; }
  .contact__name { color: #ffffff; }
  .contact__number { color: var(--ink); }
  .contact__icon { position: absolute; left: 50%; top: -22px; width: 44px; height: 44px; margin-left: -22px; }
</style>
</head>
<body>

<section class="card card--front">
  <div class="brand">
    <span class="brand__dot"></span>
    <span class="brand__name">HALLORAN FIELD<br>SERVICES</span>
  </div>
  <h1 class="headline">
    <span class="headline__top">CUSTOMIZED</span>
    <span class="headline__bottom">SPREADING</span>
  </h1>
  <div class="field" role="img" aria-label="Golden wheat field illustration"></div>
  <div class="contact">
    <svg class="contact__icon" viewBox="0 0 44 44" aria-hidden="true">
      <circle cx="22" cy="22" r="20" fill="#4d4d4f" stroke="#fff" stroke-width="3"/>
      <path d="M15 13c1.5-1 3-.5 3.5 1l1.2 3c.4 1-.2 2-1 2.5l-1 .6c.9 2.3 2.6 4 4.9 5l.6-1c.5-.8 1.5-1.4 2.5-1l3 1.2c1.5.6 2 2 1 3.5-1.2 1.8-3.2 2.6-5.2 2-5.2-1.6-9.4-5.8-11-11-.6-2 .3-4 1.5-5.8z" fill="#fff"/>
    </svg>
    <span class="contact__name">GUS</span> <span class="contact__number">0417 552 308</span>
  </div>
</section>

<section class="card card--back">
  <div class="brand">
    <span class="brand__dot"></span>
    <span class="brand__name">HALLORAN FIELD<br>SERVICES</span>
  </div>
  <ul class="services">
    <li class="service">
      <svg class="service__tick" viewBox="0 0 24 24" aria-hidden="true"><rect x="2" y="5" width="16" height="16" fill="none" stroke="#f7941d" stroke-width="2.4"/><path d="M6 12l4 4 11-13" fill="none" stroke="#f7941d" stroke-width="3"/></svg>
      <span class="service__title">BULK FERTILIZER</span>
      <span class="service__detail"><em>including</em> Lime, Gypsum,<br>Manure &amp; Compost</span>
    </li>
    <li class="service">
      <svg class="service__tick" viewBox="0 0 24 24" aria-hidden="true"><rect x="2" y="5" width="16" height="16" fill="none" stroke="#f7941d" stroke-width="2.4"/><path d="M6 12l4 4 11-13" fill="none" stroke="#f7941d" stroke-width="3"/></svg>
      <span class="service__title">MODERN EQUIPMENT</span>
      <span class="service__detail">Autosteer &amp; Variable<br>Rate Capable</span>
    </li>
    <li class="service">
      <svg class="service__tick" viewBox="0 0 24 24" aria-hidden="true"><rect x="2" y="5" width="16" height="16" fill="none" stroke="#f7941d" stroke-width="2.4"/><path d="M6 12l4 4 11-13" fill="none" stroke="#f7941d" stroke-width="3"/></svg>
      <span class="service__title">GRANULAR FERTILIZER</span>
      <span class="service__detail"><em>including</em> Single Super, Urea,<br>Gran-am, &amp; Custom Blends</span>
    </li>
    <li class="service">
      <svg class="service__tick" viewBox="0 0 24 24" aria-hidden="true"><rect x="2" y="5" width="16" height="16" fill="none" stroke="#f7941d" stroke-width="2.4"/><path d="M6 12l4 4 11-13" fill="none" stroke="#f7941d" stroke-width="3"/></svg>
      <span class="service__title">FRIENDLY &amp; RELIABLE<br>SERVICES</span>
    </li>
  </ul>
  <div class="field" role="img" aria-label="Golden wheat field illustration"></div>
  <div class="contact">
    <svg class="contact__icon" viewBox="0 0 44 44" aria-hidden="true">
      <circle cx="22" cy="22" r="20" fill="#4d4d4f" stroke="#fff" stroke-width="3"/>
      <path d="M15 13c1.5-1 3-.5 3.5 1l1.2 3c.4 1-.2 2-1 2.5l-1 .6c.9 2.3 2.6 4 4.9 5l.6-1c.5-.8 1.5-1.4 2.5-1l3 1.2c1.5.6 2 2 1 3.5-1.2 1.8-3.2 2.6-5.2 2-5.2-1.6-9.4-5.8-11-11-.6-2 .3-4 1.5-5.8z" fill="#fff"/>
    </svg>
    <span class="contact__name">GUS</span> <span class="contact__number">0417 552 308</span>
  </div>
</section>

</body>
</html>
```